Welcome Center Signage/logo Design with Multicultural Relevance

We are looking to have a welcome signage/logo designed for our church lobby with either the word "welcome" or "Welcome to the Maplecrest FSW Church!"

This design must include our organizational logo (attached). It could (but does not need to) also include our church vision: "Our vision is to be a thriving diverse urban church sharing Christ's love and serving the needs of our local and global communities." The logo/signage will be printed on 4' x 6' stretch fabric.

This signage will then be hung up behind our welcome center...it will be one of the first things people see upon entering our building.

We are an urban multicultural church that has significant outreach into our local community, one that is quite culturally diverse. If you would like more information about our church, please visit www.maplecrestfsw.org.
Updates

Project Deadline Extended
Reason: We have committed to continue work with the designers on designs submitted over the last several days, and are scheduling the additional time needed to do so. Thank you!

Target Market(s)

Culturally (African American, Hispanic American, Asian American, European American) diverse millennials and iGens

Industry/Entity Type

Church

Font styles to use
Sans Serif

Requirements
Must have
• Our logo
Nice to have
• "Welcome" in many languages
Should not have
• I can't think of anything at the moment.

```html
<!DOCTYPE html>
<html lang="en">
<head>
<meta charset="utf-8">
<title>Welcome – Maplecrest FSW Church</title>
<link rel="stylesheet" href="https://fonts.googleapis.com/css2?family=Arimo:wght@700&family=Noto+Serif+TC:wght@400&display=swap">
<style>
  :root {
    --navy: #162c44;
    --map-blue: #26507e;
    --gold: #d6a845;
    --emblem-fill: #4a2638;
  }
  html, body {
    margin: 0;
    padding: 0;
    width: 1200px;
    height: 839px;
    overflow: hidden;
    background: var(--navy);
  }
  .sign {
    position: relative;
    width: 1200px;
    height: 839px;
    background: var(--navy);
    overflow: hidden;
    font-family: "Arimo", Arial, sans-serif;
  }
  .world-map {
    position: absolute;
    left: 68px;
    top: 34px;
    width: 1064px;
    height: 694px;
    border-radius: 46% 42% 48% 40%;
    background: radial-gradient(ellipse at 50% 45%, rgba(38, 80, 126, 0.75) 0%, rgba(38, 80, 126, 0.45) 55%, rgba(38, 80, 126, 0) 75%);
  }
  .church-mark {
    position: absolute;
    left: 400px;
    top: 46px;
    width: 400px;
    height: 400px;
    border-radius: 50%;
    background: var(--emblem-fill);
    display: flex;
    align-items: center;
    justify-content: center;
  }
  .church-name {
    margin: 0;
    color: var(--gold);
    font-weight: 700;
    font-size: 42px;
    line-height: 1.2;
    text-align: center;
  }
  .greetings {
    position: absolute;
    left: 0;
    right: 0;
    margin: 0;
    text-align: center;
    color: var(--gold);
    font-weight: 700;
    font-size: 56px;
    line-height: 1;
    letter-spacing: -0.3px;
  }
  .greetings--first { top: 543px; }
  .greetings--second { top: 646px; }
  .greetings--chinese {
    top: 716px;
    font-family: "Noto Serif TC", serif;
    font-weight: 400;
    font-size: 52px;
    letter-spacing: 2px;
  }
</style>
</head>
<body>
  <main class="sign">
    <div class="world-map" role="img" aria-label="Dotted world map in soft blue behind the welcome message"></div>

    <div class="church-mark">
      <p class="church-name">Maplecrest<br>FSW Church</p>
    </div>

    <p class="greetings greetings--first">Welcome! Bienvenido! Välkommen!</p>
    <p class="greetings greetings--second">Herzlich Willkommen!</p>
    <p class="greetings greetings--chinese" lang="zh-Hant">歡迎！</p>
  </main>
</body>
</html>
```